Up to the Challenge - PPT Template with Splash Slide

We are looking for a PPT template that has 4 slides.
1. Splash slide (Creative, fun, no content, a visual representation of the theme)
2. Section header slide
3. Content Slide
4. Content Slide, another design option
The theme is 'UP to the Challenge'. The design should reflect this theme.
The colors should be in Purple (#864B99), Blue (#0A80C2), and Green (#52B054).

```html
<!DOCTYPE html>
<html lang="en">
<head>
<meta charset="utf-8">
<title>Up to the Challenge – Slide Template</title>
<link href="https://fonts.googleapis.com/css2?family=Lato:wght@700;900&family=Roboto:wght@400;500&display=swap" rel="stylesheet">
<style>
:root{
  --purple:#864B99;
  --blue:#0A80C2;
  --green:#52B054;
  --page:#f4f4f4;
  --ink:#333;
  --white:#fff;
  --brand-gradient:linear-gradient(62deg,#8a4b9c 0%,#5d5fb0 45%,#1c7cc4 80%,#0a84c6 100%);
  --bar-gradient:linear-gradient(90deg,#864B99 0%,#4d63ad 50%,#0A80C2 100%);
}
*{box-sizing:border-box;margin:0;padding:0}
html,body{width:1026px;height:1200px;overflow:hidden;background:var(--page)}
body{position:relative;font-family:'Roboto',Arial,sans-serif;color:var(--ink)}
.slide{position:absolute;width:444px;height:250px;overflow:hidden;background:var(--white);box-shadow:0 2px 10px rgba(0,0,0,.12)}
.col-left{left:51px}.col-right{left:531px}
.row-1{top:54px}.row-2{top:335px}.row-3{top:616px}.row-4{top:897px}
.slide--brand{background:var(--brand-gradient)}
.heading{font-family:'Lato',Arial,sans-serif;font-weight:700;text-transform:uppercase;letter-spacing:-.2px}
.t-purple{color:var(--purple)}.t-blue{color:var(--blue)}.t-white{color:var(--white)}

/* footer bar */
.footer-bar{position:absolute;left:94px;top:224px;width:323px;height:16px;border-radius:8px;background:var(--white);display:flex;align-items:center;padding-left:10px;font-size:4.8px;color:#333;gap:5px}
.footer-bar--gradient{background:var(--bar-gradient);color:var(--white)}
.footer-bar svg{width:5px;height:5px;flex:none}
.footer-bar .sep{margin:0 3px}
.page-no{position:absolute;right:2px;top:2px;width:12px;height:12px;border-radius:50%;background:var(--green);color:var(--white);font-size:4.4px;font-weight:500;display:flex;align-items:center;justify-content:center}
.footer-bar--gradient .page-no{background:var(--white);color:#222;border:1px solid #ddd}

/* title rule */
.title{position:absolute;left:25px;top:15px;font-size:16px}
.title-rule{position:absolute;left:0;top:40px;width:75px;height:1.2px;background:var(--green)}
.title-rule::after{content:"";position:absolute;right:-3px;top:-2.5px;width:6px;height:6px;border-radius:50%;background:var(--green)}

/* body copy */
.copy{font-size:5.2px;line-height:9px;text-align:justify}
.copy p+p{margin-top:5px}
.copy--white{color:var(--white)}
.bullets{list-style:none;font-size:5.2px;line-height:9px;text-align:justify}
.bullets li{position:relative;padding-left:12px}
.bullets li+li{margin-top:5px}
.bullets li::before{content:"";position:absolute;left:0;top:2px;width:5px;height:5px;border-radius:50%;background:var(--green)}
.bullets li::after{content:"";position:absolute;left:1.3px;top:4.2px;width:2.2px;height:.7px;background:var(--white)}

.photo{position:absolute}
</style>
</head>
<body>

<!-- Slide 1: splash / title -->
<section class="slide slide--brand col-left row-1">
  <h1 class="heading t-white" style="position:absolute;left:25px;top:102px;font-size:21px;line-height:23px">Presentation<br>Title</h1>
  <svg class="photo" width="444" height="250" viewBox="0 0 444 250" style="left:0;top:0">
    <circle cx="362" cy="93" r="137" fill="#fff"/>
    <defs>
      <linearGradient id="hikerTone" x1="0" y1="0" x2="0" y2="1">
        <stop offset="0" stop-color="#c9d5df"/>
        <stop offset=".55" stop-color="#c38552"/>
        <stop offset="1" stop-color="#5a5048"/>
      </linearGradient>
    </defs>
    <circle cx="370" cy="93" r="124" fill="url(#hikerTone)" role="img" aria-label="Hiker with a large backpack and trekking poles climbing a mountain trail"/>
  </svg>
  <div class="footer-bar">
    <svg viewBox="0 0 10 10"><path d="M2 1l2 2-1 1.3c.6 1.2 1.5 2.1 2.7 2.7L7 6l2 2-1.3 1.5C4.5 9 1 5.5.5 2.3z" fill="#0A80C2"/></svg>
    <span>+1 (888) 888 8888</span><span class="sep">|</span>
    <svg viewBox="0 0 10 10"><path d="M5 .5a3.3 3.3 0 0 0-3.3 3.3C1.7 6.5 5 9.5 5 9.5s3.3-3 3.3-5.7A3.3 3.3 0 0 0 5 .5zm0 4.6a1.2 1.2 0 1 1 0-2.4 1.2 1.2 0 0 1 0 2.4z" fill="#0A80C2"/></svg>
    <span>Lorum Ipsum Dolore Sed, USA</span>
    <span class="page-no">01</span>
  </div>
</section>

<!-- Slide 2: alternate title -->
<section class="slide col-right row-1">
  <div class="photo" role="img" aria-label="Businesswoman with a telescope standing on a tall pillar above a city skyline" style="left:0;top:0;width:444px;height:250px;background:linear-gradient(180deg,#cfe8f2 0%,#e4f1f6 55%,#b6bfc4 78%,#8e979c 100%)"></div>
  <div class="photo" role="img" aria-label="Tall dark pillar" style="left:67px;top:150px;width:42px;height:100px;background:linear-gradient(90deg,#3c4652,#5b6674)"></div>
  <h1 class="heading" style="position:absolute;left:221px;top:103px;font-size:18.5px;line-height:21px"><span class="t-purple">Presentation</span><br><span class="t-blue">Title</span></h1>
</section>

<!-- Slide 3: section header, light -->
<section class="slide col-left row-2">
  <h2 class="heading" style="position:absolute;left:0;width:444px;top:112px;text-align:center;font-size:23px"><span class="t-purple">Section</span> <span class="t-blue">Header</span></h2>
  <div class="footer-bar footer-bar--gradient">
    <svg viewBox="0 0 10 10"><path d="M2 1l2 2-1 1.3c.6 1.2 1.5 2.1 2.7 2.7L7 6l2 2-1.3 1.5C4.5 9 1 5.5.5 2.3z" fill="#52B054"/></svg>
    <span>+1 (888) 888 8888</span><span class="sep">|</span>
    <svg viewBox="0 0 10 10"><path d="M5 .5a3.3 3.3 0 0 0-3.3 3.3C1.7 6.5 5 9.5 5 9.5s3.3-3 3.3-5.7A3.3 3.3 0 0 0 5 .5zm0 4.6a1.2 1.2 0 1 1 0-2.4 1.2 1.2 0 0 1 0 2.4z" fill="#52B054"/></svg>
    <span>Lorum Ipsum Dolore Sed, USA</span>
    <span class="page-no">03</span>
  </div>
</section>

<!-- Slide 4: section header, brand -->
<section class="slide slide--brand col-right row-2">
  <h2 class="heading t-white" style="position:absolute;left:0;width:444px;top:112px;text-align:center;font-size:23px">Section Header</h2>
  <div class="footer-bar">
    <svg viewBox="0 0 10 10"><path d="M2 1l2 2-1 1.3c.6 1.2 1.5 2.1 2.7 2.7L7 6l2 2-1.3 1.5C4.5 9 1 5.5.5 2.3z" fill="#0A80C2"/></svg>
    <span>+1 (888) 888 8888</span><span class="sep">|</span>
    <svg viewBox="0 0 10 10"><path d="M5 .5a3.3 3.3 0 0 0-3.3 3.3C1.7 6.5 5 9.5 5 9.5s3.3-3 3.3-5.7A3.3 3.3 0 0 0 5 .5zm0 4.6a1.2 1.2 0 1 1 0-2.4 1.2 1.2 0 0 1 0 2.4z" fill="#0A80C2"/></svg>
    <span>Lorum Ipsum Dolore Sed, USA</span>
    <span class="page-no">04</span>
  </div>
</section>

<!-- Slide 5: about us -->
<section class="slide slide--brand col-left row-3">
  <h2 class="heading t-white title">About Us</h2>
  <div class="title-rule"></div>
  <div class="copy copy--white" style="position:absolute;left:25px;top:57px;width:190px">
    <p>Lorem ipsum dolor sit amet, consectetur adipiscing elit, sed do eiusmod tempor incididunt ut labore et dolore magna aliqua. Ut enim ad minim veniam, quis nostrud exercitation ullamco laboris nisi ut aliquip ex ea commodo consequat. Duis aute irure dolor in reprehenderit in voluptate velit esse cillum dolore eu fugiat nulla pariatur. Excepteur sint occaecat cupidatat non proiden sunt in culpa qui officia desea.</p>
    <p>Lorem ipsum dolor sit amet, consectetur adipiscing elit, sed do eiusmod tempor incididunt ut labore et dolore magna aliqua. Ut enim ad minim veniam, quis nostrud exercitation ullamco laborisea.</p>
    <p>Lorem ipsum dolor sit amet, consectetur adipiscing elit, sed do eiusmod tempor incididunt ut labore et dolore magna aliquea.</p>
    <p>Lorem ipsum dolor sit amet, consectetur adipiscing elit, sed do eiusmod tempor incididunt ut labore et dolore magna aliqua. Ut enim ad minim veniam, quis nostrud exercitation ullamco exercitation ullamco laboris nisi ut aliquip ex ea commodo laborisea.</p>
  </div>
  <div class="copy copy--white" style="position:absolute;left:229px;top:57px;width:190px">
    <p>Lorem ipsum dolor sit amet, consectetur adipiscing elit, sed do eiusmod tempor incididunt ut labore et dolore magna aliqua. Ut enim ad minim veniam, quis nostrud exercitation ullamco laboris nisi ut aliquip ex ea commodo consequat. Duis aute irure dolor in reprehenderit in voluptate velit esse cillum dolore eu fugiat nulla pariatur. Excepteur sint occaecat cupidatat non proiden sunt in culpa qui officia desea.</p>
    <p>Lorem ipsum dolor sit amet, consectetur adipiscing elit, sed do eiusmod tempor incididunt ut labore et dolore magna aliqua. Ut enim ad minim veniam, quis nostrud exercitation ullamco laborisea.</p>
    <p>Lorem ipsum dolor sit amet, consectetur adipiscing elit, sed do eiusmod tempor incididunt ut labore et dolore magna aliquea.</p>
    <p>Lorem ipsum dolor sit amet, consectetur adipiscing elit, sed do eiusmod tempor incididunt ut labore et dolore magna aliqua. Ut enim ad minim veniam, quis nostrud exercitation ullamco exercitation ullamco laboris nisi ut aliquip ex ea commodo laborisea.</p>
  </div>
  <div class="footer-bar">
    <svg viewBox="0 0 10 10"><path d="M2 1l2 2-1 1.3c.6 1.2 1.5 2.1 2.7 2.7L7 6l2 2-1.3 1.5C4.5 9 1 5.5.5 2.3z" fill="#0A80C2"/></svg>
    <span>+1 (888) 888 8888</span><span class="sep">|</span>
    <svg viewBox="0 0 10 10"><path d="M5 .5a3.3 3.3 0 0 0-3.3 3.3C1.7 6.5 5 9.5 5 9.5s3.3-3 3.3-5.7A3.3 3.3 0 0 0 5 .5zm0 4.6a1.2 1.2 0 1 1 0-2.4 1.2 1.2 0 0 1 0 2.4z" fill="#0A80C2"/></svg>
    <span>Lorum Ipsum Dolore Sed, USA</span>
    <span class="page-no">05</span>
  </div>
</section>

<!-- Slide 6: our benefits -->
<section class="slide col-right row-3">
  <h2 class="heading title"><span class="t-purple">Our</span> <span class="t-blue">Benefits</span></h2>
  <div class="title-rule"></div>
  <ul class="bullets" style="position:absolute;left:25px;top:57px;width:190px">
    <li>Lorem ipsum dolor sit amet, consectetur adipiscing elit, sed do eiusmod tempor incididunt ut labore et dolore magna aliqua. Ut enim ad minim veniam, quis nostrud exercitation ullamco laboris nisi ut aliquip ex ea commodo consequat. Duis aute irure dolor in reprehenderit in voluptate velit esse cillum dolore eu fugiatea.</li>
    <li>Lorem ipsum dolor sit amet, consectetur adipiscing elit, sed do eiusmod tempor incididunt ut labore et dolore magna aliqua. Ut enim ad minim veniam, quis nostrud exercitation ullamco laboris nisi ut aliquip ex ea commodo consequat.</li>
    <li>Lorem ipsum dolor sit amet, consectetur adipiscing elit, sed do eiusmod tempor incididunt ut labore et dolore magna aliqua. Ut enim ad minim veniam, quis nostrud exercitation ullamco laboris nisi ut aliquip ex ea commodo consequat. Duis aute irure dolor in reprehenderit in voluptate velit esse cillum dolore eu fugiatea.</li>
    <li>Lorem ipsum dolor sit amet, consectetur adipiscing elit, sed do eiusmod tempor incididunt ut labore et dolore magna aliqua.</li>
  </ul>
  <ul class="bullets" style="position:absolute;left:229px;top:57px;width:190px">
    <li>Lorem ipsum dolor sit amet, consectetur adipiscing elit, sed do eiusmod tempor incididunt ut labore et dolore magna aliqua. Ut enim ad minim veniam, quis nostrud exercitation ullamco laboris nisi ut aliquip ex ea commodo consequat. Duis aute irure dolor in reprehenderit in voluptate velit esse cillum dolore eu fugiatea.</li>
    <li>Lorem ipsum dolor sit amet, consectetur adipiscing elit, sed do eiusmod tempor incididunt ut labore et dolore magna aliqua. Ut enim ad minim veniam, quis nostrud exercitation ullamco laboris nisi ut aliquip ex ea commodo consequat.</li>
    <li>Lorem ipsum dolor sit amet, consectetur adipiscing elit, sed do eiusmod tempor incididunt ut labore et dolore magna aliqua. Ut enim ad minim veniam, quis nostrud exercitation ullamco laboris nisi ut aliquip ex ea commodo consequat. Duis aute irure dolor in reprehenderit in voluptate velit esse cillum dolore eu fugiatea.</li>
    <li>Lorem ipsum dolor sit amet, consectetur adipiscing elit, sed do eiusmod tempor incididunt ut labore et dolore magna aliqua.</li>
  </ul>
  <div class="footer-bar footer-bar--gradient">
    <svg viewBox="0 0 10 10"><path d="M2 1l2 2-1 1.3c.6 1.2 1.5 2.1 2.7 2.7L7 6l2 2-1.3 1.5C4.5 9 1 5.5.5 2.3z" fill="#52B054"/></svg>
    <span>+1 (888) 888 8888</span><span class="sep">|</span>
    <svg viewBox="0 0 10 10"><path d="M5 .5a3.3 3.3 0 0 0-3.3 3.3C1.7 6.5 5 9.5 5 9.5s3.3-3 3.3-5.7A3.3 3.3 0 0 0 5 .5zm0 4.6a1.2 1.2 0 1 1 0-2.4 1.2 1.2 0 0 1 0 2.4z" fill="#52B054"/></svg>
    <span>Lorum Ipsum Dolore Sed, USA</span>
    <span class="page-no">06</span>
  </div>
</section>

<!-- Slide 7: who we are -->
<section class="slide col-left row-4">
  <h2 class="heading title"><span class="t-purple">Who</span> <span class="t-blue">We Are</span></h2>
  <div class="title-rule"></div>
  <div class="photo" role="img" aria-label="Climbers helping each other up a rocky ridge at sunset" style="left:25px;top:64px;width:186px;height:139px;border-radius:8px;background:linear-gradient(160deg,#6b7784 0%,#c98a5a 45%,#e8a35f 55%,#3a3632 85%)"></div>
  <ul class="bullets" style="position:absolute;left:229px;top:78px;width:190px">
    <li>Lorem ipsum dolor sit amet, consectetur adipiscing elit, sed do eiusmod tempor incididunt ut labore et dolore magna aliqua. Ut enim ad minim veniam, quis nostrud exercitation ullamco laboris nisi ut aliquip ex ea commodo consequat. Duis aute irure dolor in reprehenderit in voluptate velit esse cillum dolore eu fugiatea.</li>
    <li>Lorem ipsum dolor sit amet, consectetur adipiscing elit, sed do eiusmod tempor incididunt ut labore et dolore magna aliqua. Ut enim ad minim veniam, quis nostrud exercitation ullamco laboris nisi ut aliquip ex ea commodo consequat.</li>
    <li>Lorem ipsum dolor sit amet, consectetur adipiscing elit, sed do eiusmod tempor incididunt ut labore et dolore magna aliqua.</li>
  </ul>
  <div class="footer-bar footer-bar--gradient">
    <svg viewBox="0 0 10 10"><path d="M2 1l2 2-1 1.3c.6 1.2 1.5 2.1 2.7 2.7L7 6l2 2-1.3 1.5C4.5 9 1 5.5.5 2.3z" fill="#52B054"/></svg>
    <span>+1 (888) 888 8888</span><span class="sep">|</span>
    <svg viewBox="0 0 10 10"><path d="M5 .5a3.3 3.3 0 0 0-3.3 3.3C1.7 6.5 5 9.5 5 9.5s3.3-3 3.3-5.7A3.3 3.3 0 0 0 5 .5zm0 4.6a1.2 1.2 0 1 1 0-2.4 1.2 1.2 0 0 1 0 2.4z" fill="#52B054"/></svg>
    <span>Lorum Ipsum Dolore Sed, USA</span>
    <span class="page-no">07</span>
  </div>
</section>

<!-- Slide 8: what we do -->
<section class="slide slide--brand col-right row-4">
  <h2 class="heading t-white title">What We Do</h2>
  <div class="title-rule"></div>
  <p class="copy copy--white" style="position:absolute;left:40px;top:62px;width:364px;text-align:center">Lorem ipsum dolor sit amet, consectetur adipiscing elit, sed do eiusmod tempor incididunt ut labore et dolore magna aliqua. Ut enim ad minim veniam, quis nostrud exercitation ullamco laboris nisi ut aliquip ex ea commodo consequat. Duis aute irure dolor in reprehenderit in voluptate velit esse cillum dolore eu fugiat nulla pariatur excepteur sint occaecat cupidatat non ullamco laboris nisi ut aliquip ex ea commodo consequat. Duis aute irure dolor in reprehenderit in voluptate velit esse cillum dolore proidentea.</p>
  <div class="photo" role="img" aria-label="Road with a start marking leading toward a sunrise" style="left:25px;top:111px;width:123px;height:90px;border:1.5px solid #fff;border-radius:7px;background:linear-gradient(180deg,#c9c2a8 0%,#e9d7a8 40%,#37404a 60%,#1c2128 100%)"></div>
  <div class="photo" role="img" aria-label="Person on a long stairway toward a mountain sunset" style="left:160px;top:111px;width:123px;height:90px;border:1.5px solid #fff;border-radius:7px;background:linear-gradient(180deg,#3a3a44 0%,#e3a05a 40%,#8a5a3c 65%,#2e2a28 100%)"></div>
  <div class="photo" role="img" aria-label="Hand placing wooden blocks as rising steps" style="left:295px;top:111px;width:123px;height:90px;border:1.5px solid #fff;border-radius:7px;background:linear-gradient(160deg,#f4f1ee 0%,#ece4dc 55%,#d9b789 70%,#e3ddd6 100%)"></div>
  <div class="footer-bar">
    <svg viewBox="0 0 10 10"><path d="M2 1l2 2-1 1.3c.6 1.2 1.5 2.1 2.7 2.7L7 6l2 2-1.3 1.5C4.5 9 1 5.5.5 2.3z" fill="#0A80C2"/></svg>
    <span>+1 (888) 888 8888</span><span class="sep">|</span>
    <svg viewBox="0 0 10 10"><path d="M5 .5a3.3 3.3 0 0 0-3.3 3.3C1.7 6.5 5 9.5 5 9.5s3.3-3 3.3-5.7A3.3 3.3 0 0 0 5 .5zm0 4.6a1.2 1.2 0 1 1 0-2.4 1.2 1.2 0 0 1 0 2.4z" fill="#0A80C2"/></svg>
    <span>Lorum Ipsum Dolore Sed, USA</span>
    <span class="page-no">08</span>
  </div>
</section>

</body>
</html>
```